Brightfen Business Card Redesign & Logo Update

We need to update our business cards to something more modern and fresh. Brightfen can provide the current color schemes and old design examples, but welcome creativity in helping us with this redesign. PLEASE NOTE that we no longer utilize the "tree" and/or "leaf" imagery in our branding. If able would apprecaite an update on the quality of our "words only" logo in Ai. / PNG formats too.

Target Market(s)

Investors, landowners, corporate partners, contractors

Industry/Entity Type

Environmental Restoration & Conservation

Contact Information for Business Card

Logo, persons name, title, mailing address, phone and email, website url

Font styles to use
Other font styles liked:
• Merriweather

Requirements
Nice to have
• Logo, persons name, title, mailing address, phone and email, website url, but open to ideams
Should not have
• No all back backgrounds

```html
<!DOCTYPE html>
<html lang="en">
<head>
<meta charset="utf-8">
<title>Brightfen Business Card</title>
<link href="https://fonts.googleapis.com/css2?family=Open+Sans:wght@400;600;700;800&display=swap" rel="stylesheet">
<style>
  :root {
    --brand-green: #177d3c;
    --brand-orange: #ee7d22;
    --name-orange: #ee5a24;
    --ink: #1f1f1f;
    --paper: #ffffff;
    --backdrop: #2b2d30;
  }
  * { box-sizing: border-box; margin: 0; padding: 0; }
  html, body {
    width: 1200px; height: 780px; overflow: hidden;
    background: var(--backdrop);
    font-family: "Open Sans", Arial, sans-serif;
  }
  .canvas {
    width: 1200px; height: 780px;
    display: flex; align-items: center; justify-content: center; gap: 40px;
  }
  .card {
    position: relative;
    width: 540px; height: 310px;
    border-radius: 24px;
    overflow: hidden;
  }
  .card-back { background: var(--brand-green); }
  .back-pattern { position: absolute; inset: 0; background: var(--brand-green); }
  .back-wordmark {
    position: absolute; left: 330px; top: 178px;
    color: var(--paper); font-weight: 800; font-size: 26px; letter-spacing: 0.5px;
    white-space: nowrap;
  }
  .card-front { background: var(--paper); }
  .front-bands { position: absolute; inset: 0; }
  .front-wordmark {
    position: absolute; left: 34px; top: 160px;
    color: var(--brand-green); font-weight: 800; font-size: 46px; line-height: 1;
    letter-spacing: -0.5px; white-space: nowrap;
  }
  .divider {
    position: absolute; left: 288px; top: 84px;
    width: 1px; height: 120px; background: var(--ink);
    transform: rotate(-8deg);
  }
  .person { position: absolute; left: 318px; top: 78px; }
  .person-name { font-size: 22px; font-weight: 800; line-height: 1.1; white-space: nowrap; }
  .person-name .first { color: var(--name-orange); }
  .person-name .last { color: var(--brand-green); }
  .person-title { font-size: 13px; color: var(--ink); margin-top: 4px; }
  .contacts { list-style: none; margin-top: 16px; }
  .contacts li {
    display: flex; align-items: center; gap: 8px;
    font-size: 12px; color: var(--ink); margin-bottom: 5px;
  }
  .contacts svg { width: 13px; height: 13px; flex: none; }
</style>
</head>
<body>
<main class="canvas">
  <section class="card card-back">
    <div class="back-pattern" role="img" aria-label="Repeated brand name pattern in darker green"></div>
    <div class="back-wordmark">Brightfen</div>
  </section>

  <section class="card card-front">
    <svg class="front-bands" viewBox="0 0 540 310" aria-hidden="true">
      <polygon points="0,284 340,284 360,310 0,310" fill="var(--brand-orange)"/>
      <polygon points="322,262 540,232 540,310 388,310" fill="var(--brand-green)"/>
    </svg>
    <div class="front-wordmark">Brightfen</div>
    <div class="divider"></div>
    <div class="person">
      <h1 class="person-name"><span class="first">Marta</span> <span class="last">Velinska</span></h1>
      <p class="person-title">Managing Director</p>
      <ul class="contacts">
        <li>
          <svg viewBox="0 0 16 16"><path fill="var(--name-orange)" d="M3.6 1.5 6 4 4.8 5.6c.8 2 2.5 3.7 4.6 4.6L11 9l2.5 2.4-1.3 2.3C7 13.5 2.5 9 2.3 3.8z"/></svg>
          (555) 014-2758
        </li>
        <li>
          <svg viewBox="0 0 16 16"><rect x="1.5" y="3.5" width="13" height="9" rx="1" fill="var(--name-orange)"/><path d="M2 4l6 5 6-5" stroke="#fff" stroke-width="1.3" fill="none"/></svg>
          info@website.com
        </li>
        <li>
          <svg viewBox="0 0 16 16"><circle cx="8" cy="8" r="6.5" fill="var(--name-orange)"/><path d="M1.5 8h13M8 1.5c-2.5 3-2.5 10 0 13M8 1.5c2.5 3 2.5 10 0 13" stroke="#fff" stroke-width="1" fill="none"/></svg>
          www.website.com
        </li>
      </ul>
    </div>
  </section>
</main>
</body>
</html>
```